Redesign two existing website pages and one new landing page for dental office

I need to redesign two webpages on my dental website, the Home page (http://velbridgedental.com) and the Dental Implant Services page (http://www.velbridgedental.com/dental-implant-services) and also create a landing page for the Dental Implant Services page.

Please use the same color scheme, slogans and subtitles for the redesign pages and create a reserved video spot on each page. The video spots should not be too big but not too small either and positioned in a central key location on each of the pages. The final redesigned pages should communicate leadership, confidence and trust.

The new landing page for the Dental implant Services page must not have any hyperlinks on the page and must entice the viewer to give name and email before downloading a "Free" eBook called "Is a Fuller Smile Worth the Wait?" Any added photo images to this new page must be smiling.
Updates

Project Deadline Extended Reason: I got feedback that my project was not long enough so I'm extending it by 5 days. Added Thursday, April 16, 2015

Target Market(s)

People who are middle-age to seniors.

Industry/Entity Type

Dental

Coding

Coded - Design and coding required

Number of Pages Required

3 page

Requirements
Must have
• Compatible with existing website colors and theme.

```html
<!DOCTYPE html>
<html lang="en">
<head>
<meta charset="utf-8">
<title>Velbridge Dental Care</title>
<link href="https://fonts.googleapis.com/css2?family=Raleway:wght@400;500;600&family=Open+Sans:wght@400;600&display=swap" rel="stylesheet">
<style>
:root{
  --green:#5f9080;
  --green-dark:#46705f;
  --green-light:#7fae9c;
  --teal:#45bfc2;
  --ink:#333;
  --ink-soft:#555;
  --sub:#4f9a86;
  --mint:#eaf3ef;
  --white:#fff;
}
*{box-sizing:border-box;margin:0;padding:0}
html,body{width:786px;height:1200px;overflow:hidden;background:var(--white)}
body{position:relative;font-family:"Open Sans",sans-serif;color:var(--ink)}
.abs{position:absolute}
.header .brand{left:146px;top:26px;font-family:"Raleway",sans-serif;font-size:19px;font-weight:500;color:var(--green);display:flex;align-items:center;gap:6px}
.header .brand i{width:8px;height:8px;border-radius:50%;background:var(--green);display:block}
.call{right:134px;top:26px;text-align:right;font-family:"Raleway",sans-serif}
.call small{display:block;font-size:10px;color:var(--sub)}
.call b{font-weight:500;font-size:13px;color:var(--ink);display:flex;align-items:center;gap:4px;justify-content:flex-end}
.nav{left:0;top:64px;width:786px;height:28px;background:linear-gradient(#7aa796,#5e8f7d)}
.nav ul{list-style:none;display:flex;position:absolute;left:139px;top:0;height:28px}
.nav li{font-family:"Raleway",sans-serif;font-size:8.5px;font-weight:600;color:#fff;padding:0 18px;line-height:28px;border-right:1px solid rgba(255,255,255,.25)}
.nav li.active{background:#4f7c6b}
.hero{left:0;top:92px;width:786px;height:270px;background:linear-gradient(100deg,#dfe5ea 0%,#c9d4dc 40%,#a9b9c8 70%,#e3e8ec 100%)}
.hero-box{left:125px;top:174px;width:244px;height:101px;background:rgba(38,62,54,.88);padding:18px 23px}
.hero-box h1{font-family:"Raleway",sans-serif;font-weight:400;font-size:22px;color:#fff;letter-spacing:.5px}
.hero-box p{font-family:"Raleway",sans-serif;font-size:11px;color:#fff;margin-top:3px}
.btn{display:inline-block;background:linear-gradient(#83b3a1,#5d8f7d);color:#fff;font-family:"Raleway",sans-serif;font-size:7.5px;font-weight:600;padding:6px 9px;border-radius:2px}
.hero-box .btn{margin-top:8px;font-size:8px}
.dots{left:372px;top:343px;display:flex;gap:3px}
.dots span{width:9px;height:9px;border-radius:50%;background:#fff}
.feature{top:378px;width:140px;text-align:center}
.feature svg{display:block;margin:0 auto;height:40px}
.feature h3{font-family:"Raleway",sans-serif;font-weight:500;font-size:12px;margin-top:14px;color:var(--ink)}
.feature p{font-size:6px;line-height:10px;color:var(--ink-soft);margin-top:6px}
.feature a{display:block;font-size:6.5px;font-weight:600;color:var(--ink);margin-top:3px}
.section-title{font-family:"Raleway",sans-serif;font-weight:400;font-size:17.5px;color:var(--ink)}
.section-sub{font-family:"Raleway",sans-serif;font-size:10px;color:var(--sub);margin-top:3px}
.copy p{font-size:6px;line-height:10px;color:var(--ink-soft);margin-top:6px}
.copy p.lead{font-size:6.5px}
.copy .btn{margin-top:9px;font-size:6px;padding:5px 10px}
.hygiene{left:130px;top:559px;width:310px}
.hygiene-photo{left:455px;top:507px;width:217px;height:200px;background:radial-gradient(circle at 55% 45%,#c9a48a 0,#8ab8bb 45%,#eef0f0 70%)}
.band{left:0;top:707px;width:786px;height:200px;background:var(--mint)}
.band-photo{left:1px;top:707px;width:340px;height:200px;background:linear-gradient(90deg,#9fb2c0 0%,#b9c8d3 55%,var(--mint) 100%)}
.emergency{left:350px;top:750px;width:310px}
.emergency .btn{background:#26433a}
.card{top:937px;width:167px}
.card .ph{height:86px;border:2px solid #d8dcdc;box-shadow:0 1px 2px rgba(0,0,0,.2)}
.card h3{font-family:"Raleway",sans-serif;font-weight:400;font-size:12.5px;color:var(--green-dark);margin-top:10px}
.card p{font-size:5.8px;line-height:9.6px;color:var(--ink-soft);margin-top:4px}
.footer{left:0;top:1116px;width:786px;height:84px;background:linear-gradient(#678f7f,#4e7565)}
.footer .links{left:130px;top:20px;font-family:"Raleway",sans-serif;font-size:7.5px;font-weight:600;color:#fff;word-spacing:1px}
.footer .copyright{left:130px;top:36px;font-size:6.5px;color:#fff}
.footer .social{left:130px;top:51px;display:flex;gap:3px}
.footer .social span{width:11px;height:11px;border-radius:2px;background:#fff;display:block}
.footer .address{left:524px;top:20px;font-size:6.3px;line-height:10.5px;color:#fff}
</style>
</head>
<body>
<header class="header">
  <div class="brand abs"><i></i>Velbridge Dental Care</div>
  <div class="call abs"><small>Call Us Now</small><b><svg width="9" height="9" viewBox="0 0 24 24"><path fill="#4f9a86" d="M6.6 10.8a15 15 0 0 0 6.6 6.6l2.2-2.2a1 1 0 0 1 1-.25 11.4 11.4 0 0 0 3.6.57 1 1 0 0 1 1 1V20a1 1 0 0 1-1 1A17 17 0 0 1 3 4a1 1 0 0 1 1-1h3.5a1 1 0 0 1 1 1c0 1.25.2 2.45.57 3.57a1 1 0 0 1-.25 1z"/></svg>(713) 555-0148</b></div>
</header>
<nav class="nav abs"><ul><li class="active">HOME</li><li>ABOUT US</li><li>DENTAL SERVICES</li><li>BLOG</li><li>TESTIMONIALS</li><li>CONTACT US</li></ul></nav>

<section class="hero abs" role="img" aria-label="Photo of a dentist examining a senior patient in the dental chair"></section>
<div class="hero-box abs"><h1>DENTAL CARE</h1><p>MAEDEURIS VEL LACUS VITAE FELIS</p><span class="btn">Schedule An Appointment?</span></div>
<div class="dots abs"><span></span><span></span><span></span><span></span></div>

<div class="feature abs" style="left:117px">
  <svg viewBox="0 0 64 40" width="64"><path d="M4 6c8 6 48 6 56 0-2 14-10 26-28 26S6 20 4 6z" fill="none" stroke="#45bfc2" stroke-width="3"/><path d="M14 18v8M22 20v10M32 20v11M42 20v10M50 18v8" stroke="#45bfc2" stroke-width="2.5"/></svg>
  <h3>Beautiful Dentures</h3><p>Aascetur ridiculus mus In iaculis facilisis massa Etiam eu urna Sed porta Suspendisse quam leo molest</p><a>Learn More</a></div>
<div class="feature abs" style="left:253px">
  <svg viewBox="0 0 40 40" width="40"><path d="M12 12c4-2 6 0 8 0s4-2 8 0c4 2 3 9 1 14-1 4-2 11-4 11s-2-7-5-7-3 7-5 7-3-7-4-11c-2-5-3-12 1-14z" fill="#45bfc2"/><path d="M6 2l1 3 3 1-3 1-1 3-1-3-3-1 3-1z" fill="#45bfc2"/></svg>
  <h3>Cosmetic Dentistry</h3><p>Aascetur ridiculus mus In iaculis facilisis massa Etiam eu urna Sed porta Suspendisse quam leo molest</p><a>Learn More</a></div>
<div class="feature abs" style="left:393px">
  <svg viewBox="0 0 24 40" width="24"><path d="M4 2h16c0 6-2 9-8 9S4 8 4 2z" fill="none" stroke="#45bfc2" stroke-width="2.5"/><path d="M7 14h10l-1 4H8zM8 20h8l-1 4H9zM9 26h6l-1 4h-4zM10 32h4l-2 6z" fill="#45bfc2"/></svg>
  <h3>Dental Implant Services</h3><p>Aascetur ridiculus mus In iaculis facilisis massa Etiam eu urna Sed porta Suspendisse quam leo molest</p><a>Learn More</a></div>
<div class="feature abs" style="left:529px">
  <svg viewBox="0 0 48 40" width="48"><circle cx="10" cy="7" r="4" fill="#45bfc2"/><path d="M4 16l8 12h30l2 4H10L2 18z" fill="none" stroke="#45bfc2" stroke-width="3"/><path d="M14 14l6 8h14" fill="none" stroke="#45bfc2" stroke-width="3"/><path d="M22 10l10 4" stroke="#45bfc2" stroke-width="2.5"/></svg>
  <h3>Sedation Dentistry</h3><p>Aascetur ridiculus mus In iaculis facilisis massa Etiam eu urna Sed porta Suspendisse quam leo molest</p><a>Learn More</a></div>

<section class="hygiene copy abs">
  <h2 class="section-title">Dental Hygiene Services</h2>
  <div class="section-sub">Achieve Better Health With Prevention</div>
  <p class="lead">Aascetur ridiculus mus In iaculis facilisis massa Etiam eu urna Sed porta Suspendisse</p>
  <p>Mauris vel lacus vitae felis vestibulum volutpat Etiam est nunc venenatis in tristique eu imperdiet ac nisl Cum sociis natoque penatibus et magnis dis parturient montes nascetur</p>
  <p>n massa libero interdum nec interdum vel blandit sed nulla In ullamcorper est eget tempor cursus neque</p>
  <span class="btn">READ MORE</span>
</section>
<div class="hygiene-photo abs" role="img" aria-label="Photo of a woman holding her cheek with tooth pain"></div>

<div class="band abs"></div>
<div class="band-photo abs" role="img" aria-label="Photo of a dentist and assistant showing an x-ray to a senior patient"></div>
<section class="emergency copy abs">
  <h2 class="section-title">Dental Emergency Services</h2>
  <div class="section-sub">Stop Pain From Tooth Trauma and Infection</div>
  <p class="lead">Aascetur ridiculus mus In iaculis facilisis massa Etiam eu urna Sed porta Suspendisse</p>
  <p>Mauris vel lacus vitae felis vestibulum volutpat Etiam est nunc venenatis in tristique eu imperdiet ac nisl Cum sociis natoque penatibus et magnis dis parturient montes nascetur</p>
  <p>n massa libero interdum nec interdum vel blandit sed nulla In ullamcorper est eget tempor cursus neque</p>
  <span class="btn">READ MORE</span>
</section>

<article class="card abs" style="left:130px"><div class="ph" role="img" aria-label="Photo of a woman with toothache" style="background:linear-gradient(90deg,#e9e6e2,#cdb8a8 60%,#eceae6)"></div><h3>Don't wait til it Hurts</h3><p>Morbi ornare gravida elit Integer congue augue et malesuada iaculis ipsum dui aliquet felis at cursus magna nisl nec elit Praesent elementum elit at</p></article>
<article class="card abs" style="left:308px"><div class="ph" role="img" aria-label="Photo of a smiling patient during a dental cleaning" style="background:linear-gradient(90deg,#d9b9a5,#8fb4d6 55%,#3f7fc4)"></div><h3>Recent Blogs</h3><p>Morbi ornare gravida elit Integer congue augue et malesuada iaculis ipsum dui aliquet felis at cursus magna nisl nec elit Praesent elementum elit at</p></article>
<article class="card abs" style="left:486px"><div class="ph" role="img" aria-label="Photo of the dental team in the clinic" style="background:linear-gradient(90deg,#6d9ccf,#bcd3e6 55%,#e5ecf1)"></div><h3>Dental Services</h3><p>Morbi ornare gravida elit Integer congue augue et malesuada iaculis ipsum dui aliquet felis at cursus magna nisl nec elit Praesent elementum elit at</p></article>

<footer class="footer abs">
  <div class="links abs">HOME &nbsp;| &nbsp;ABOUT US &nbsp;| &nbsp;SERVICES &nbsp;| &nbsp;CONSULTING &nbsp;| &nbsp;CLIENTS &nbsp;| &nbsp;PROJECTS &nbsp;| &nbsp;CONTACT</div>
  <div class="copyright abs">© 2015 Company Name &nbsp;All right reserved &nbsp;Term of Use</div>
  <div class="social abs"><span></span><span></span><span></span></div>
  <div class="address abs">Larkspur Medical Center, 2450 Meadow Pkwy, Ste.<br>#310, Brookfield, TX 77590<br>Phone: (713) 555-0148</div>
</footer>
</body>
</html>
```